Plakat-Design für Immobilienmakler und Baufinanzierer
Zielgruppe
Wir sind Immobilienmakler und Baufinanzierer und suchen ein hochwertiges Design, unsere Zielgruppe sind Kunden, die Ihr Haus verkaufen möchten. Für jeden erfolgreichen Verkauf spenden wir 5 % unserer Maklercourtage an einen Verein, den sich der Kunde aussuchen darf. Mit diesem Plakat wollen wir auf unsere Vereinsförderng aufmerksam machen und Vereine ansprechen.
Aufgabenstellung
Text: 'Wir spenden 5 % unserer Provision für Ihren Verein', 'Nur 1,99 % Maklercourtage', Logo, Kontaktdaten

```html
<!DOCTYPE html>
<html lang="de">
<head>
<meta charset="utf-8">
<title>Plakat – Vereinsförderung</title>
<link rel="stylesheet" href="https://fonts.googleapis.com/css2?family=Raleway:wght@400;600;700;900&display=swap">
<style>
  :root {
    --stage: #2b2e2f;
    --paper: #efece6;
    --teal: #1f4f57;
    --stone: #9a938a;
    --rule: #8f8a83;
    --ink: #2a4a50;
  }
  html, body {
    margin: 0;
    padding: 0;
    width: 1200px;
    height: 1200px;
    overflow: hidden;
    background: var(--stage);
  }
  .canvas {
    position: relative;
    width: 1200px;
    height: 1200px;
    display: flex;
    align-items: center;
    justify-content: center;
  }
  .poster {
    position: relative;
    width: 786px;
    height: 1100px;
    background: var(--paper);
    font-family: "Raleway", sans-serif;
    overflow: hidden;
  }
  .brand {
    position: absolute;
    top: 78px;
    right: 46px;
    display: flex;
    align-items: center;
    gap: 10px;
  }
  .brand-dot {
    width: 12px;
    height: 12px;
    border-radius: 50%;
    background: var(--teal);
  }
  .brand-name {
    font-size: 22px;
    font-weight: 700;
    letter-spacing: 0.12em;
    text-transform: uppercase;
    color: var(--teal);
  }
  .headline {
    position: absolute;
    top: 228px;
    left: 48px;
    margin: 0;
    font-size: 62px;
    font-weight: 900;
    line-height: 79px;
    text-transform: uppercase;
    letter-spacing: 0.005em;
  }
  .headline span { display: block; }
  .headline .accent { color: var(--teal); }
  .headline .muted { color: var(--stone); }
  .offer {
    position: absolute;
    top: 564px;
    left: 48px;
    margin: 0;
    font-size: 22px;
    font-weight: 700;
    color: var(--stone);
    text-transform: uppercase;
  }
  .offer-rule {
    position: absolute;
    top: 603px;
    left: 0;
    width: 404px;
    height: 3px;
    background: var(--rule);
  }
  .contact {
    position: absolute;
    top: 876px;
    left: 48px;
    font-size: 14.5px;
    line-height: 18px;
    color: var(--ink);
  }
  .contact p { margin: 0 0 22px; }
  .contact strong { font-weight: 700; color: var(--teal); }
</style>
</head>
<body>
<div class="canvas">
  <article class="poster">
    <div class="brand">
      <span class="brand-dot"></span>
      <span class="brand-name">Wendel Immobilien</span>
    </div>

    <h1 class="headline">
      <span class="accent">Wir spenden 5 %</span>
      <span class="muted">unserer Provision</span>
      <span class="accent">für Ihren Verein</span>
    </h1>

    <p class="offer">Nur 1,99 % Maklercourtage</p>
    <div class="offer-rule"></div>

    <address class="contact" style="font-style:normal">
      <p><strong>Wendel Immobilien</strong><br>Lindenweg 7<br>41234 Musterhain</p>
      <p>Tel: 02100 481 22 60<br>Mobil: 0151 270 448 19</p>
      <p>info@wendel-immobilien.de<br>www.wendel-immobilien.de</p>
    </address>
  </article>
</div>
</body>
</html>
```